Timber Ridge Athletics Web Design

Need to completely update website - simple and clean look - informative
this will be our main source for booking appointments etc. needs to have baseball and softball content. we currently have a site - looking to update - we would like you to design and add to our current site.

Target Market(s)

ages 15-45, youth and parents for kids- softball and baseball players /fitness

Industry/Entity Type

baseball and softball indoor training facility

Coding

Coded - Design and coding required

Number of Pages Required

5+ page

Colors

Designer to choose colors to be used in the design.

Requirements
Must have
• our colors of business are green and black- we need you to completely set up the website for us
Nice to have
• out current webiste is www.timberridge482.example

```html
<!DOCTYPE html>
<html lang="en">
<head>
<meta charset="utf-8">
<title>Timber Ridge Athletics – Baseball and Softball</title>
<link rel="stylesheet" href="https://fonts.googleapis.com/css2?family=Lato:wght@400;700;900&family=Righteous&display=swap">
<style>
:root{
  --green:#3cf01f;
  --green-dark:#1f6b12;
  --green-deep:#0e3a08;
  --black:#000;
  --ink:#0b0b0b;
  --white:#fff;
  --grey:#9a9a9a;
  --text:#d8d8d8;
}
*{box-sizing:border-box;margin:0;padding:0}
html,body{width:1200px;height:4190px;overflow:hidden;background:var(--black);font-family:'Lato',sans-serif;color:var(--white)}
.page{position:relative;width:1200px;height:4190px}
.abs{position:absolute}
.display{font-family:'Righteous',sans-serif;font-weight:400;letter-spacing:1px}

/* top bar */
.topbar{position:absolute;top:0;left:0;width:1200px;height:49px;background:var(--black)}
.topbar .green{position:absolute;left:0;top:0;width:600px;height:49px;background:var(--green)}
.social-dot{position:absolute;top:9px;width:32px;height:32px;border-radius:50%;background:var(--black)}
.topbar .contact{position:absolute;top:14px;font-size:16px;display:flex;align-items:center;gap:10px}

/* nav */
.nav{position:absolute;top:49px;left:0;width:1200px;height:86px;background:var(--white);color:#111}
.nav a{position:absolute;top:34px;font-size:15px;color:#111;text-decoration:none}
.nav a.active{color:var(--green);text-decoration:underline}
.brand{position:absolute;left:426px;top:18px;display:flex;align-items:center;gap:12px}
.brand .mark{width:52px;height:52px;border-radius:50%;background:var(--black);border:3px solid var(--green)}
.brand .name{font-family:'Lato',sans-serif;font-weight:900;font-size:26px;color:#111;letter-spacing:1px}

/* section dots */
.dots{position:absolute;left:46px;display:flex;flex-direction:column;gap:14px}
.dots span{width:12px;height:12px;border-radius:50%;background:#8a8a8a}
.dots span.on{background:var(--green)}

/* buttons */
.btn{position:absolute;background:var(--green);color:#000;font-weight:900;font-size:19px;display:flex;align-items:center;justify-content:center}
.btn::after{content:"";position:absolute;left:6px;top:6px;right:-6px;bottom:-6px;border:2px solid var(--green);border-left:0;border-top:0;pointer-events:none}

/* hero */
.hero{position:absolute;top:135px;left:0;width:1200px;height:600px;background:radial-gradient(ellipse at 72% 50%,#5a5a5a 0%,#2a2a2a 35%,#0a0a0a 75%)}
.hero h1{position:absolute;left:109px;top:112px;font-size:60px;line-height:62px}
.rule-title{display:flex;align-items:center;gap:6px;font-weight:900}
.rule-title::before,.rule-title::after{content:"";display:block;height:3px;width:40px;background:var(--white)}

/* about */
.about{position:absolute;top:735px;left:0;width:1200px;height:1008px;background:radial-gradient(ellipse at 20% 90%,#0f3a0a 0%,#050a04 40%,#000 70%)}
.badge{position:absolute;left:158px;top:30px;width:422px;height:422px;border-radius:50%;border:6px solid var(--green);display:flex;align-items:center;justify-content:center}
.badge .inner{width:388px;height:388px;border-radius:50%;border:6px solid var(--white);background:radial-gradient(circle at 50% 40%,#5ca447 0%,#2d7a1d 55%,#164d0c 100%)}
.about h2{position:absolute;left:626px;top:70px;font-size:46px}
.about .kicker{position:absolute;left:626px;top:137px;font-size:20px;font-weight:700;display:flex;align-items:center;gap:6px}
.about .kicker::after{content:"";width:40px;height:3px;background:var(--white)}
.about p{position:absolute;left:626px;top:175px;width:470px;font-size:14px;line-height:31px;color:var(--text)}
.about .sign{position:absolute;left:626px;top:425px;font-size:14px;color:var(--text)}
.about .sign em{font-style:normal;color:var(--green)}
.photo-frame{position:absolute;border:4px solid var(--green)}

/* section headings */
.sec-title{position:absolute;left:0;width:1200px;text-align:center;font-size:46px}
.sec-sub{position:absolute;left:0;width:1200px;display:flex;justify-content:center;align-items:center;gap:8px;font-size:20px;font-weight:700}
.sec-sub::before,.sec-sub::after{content:"";width:44px;height:3px;background:var(--white)}

/* lessons */
.lessons{position:absolute;top:1743px;left:0;width:1200px;height:683px;background:linear-gradient(180deg,#000 0%,#050f03 30%,#123f0b 70%,#1f6b12 100%)}
.lesson-card{position:absolute;top:192px;width:436px;height:301px}
.lesson-card .shot{position:absolute;inset:0}
.lesson-card .edge{position:absolute;left:16px;top:16px;width:436px;height:301px;border:3px solid var(--green);border-top:0;border-left-width:3px}
.lesson-card .caption{position:absolute;top:355px;left:-20px;width:490px;text-align:center;font-size:31px;line-height:33px;font-weight:700}

/* facility */
.facility{position:absolute;top:2426px;left:0;width:1200px;height:764px;background:linear-gradient(180deg,#000 0%,#0b1a08 40%,#185a0e 85%,#1f6b12 100%)}

/* contact */
.contact-sec{position:absolute;top:3190px;left:0;width:1200px;height:631px;background:linear-gradient(180deg,#000 0%,#050b04 45%,#164d0c 85%,#226f14 100%)}
.field{position:absolute;height:56px;border:2px solid var(--green-dark);background:rgba(0,0,0,.35);font-size:15px;font-weight:700;color:var(--white);padding:18px 18px}
.field.message{height:105px}
.submit{position:absolute;left:509px;top:514px;width:180px;height:55px;border-radius:28px;background:var(--green);border:3px solid #000;box-shadow:0 0 0 2px var(--green);color:#000;font-weight:900;font-size:21px;display:flex;align-items:center;justify-content:center}

/* footer */
.footer{position:absolute;top:3821px;left:0;width:1200px;height:369px;background:var(--black)}
.footer .brand-small{position:absolute;left:93px;top:118px;display:flex;align-items:center;gap:8px}
.footer .brand-small .mark{width:40px;height:40px;border-radius:50%;border:2px solid var(--white)}
.footer .brand-small .name{font-weight:900;font-size:18px;letter-spacing:1px}
.vline{position:absolute;top:74px;width:1px;height:132px;background:#555}
.fcol{position:absolute;top:70px}
.fcol h4{font-size:20px;font-weight:400;margin-bottom:14px}
.fcol .row{display:flex;gap:10px;font-size:15px;font-weight:700;line-height:25px;margin-bottom:10px}
.fcol .row svg{flex:none;margin-top:5px}
.footer .divider{position:absolute;left:109px;top:303px;width:980px;height:1px;background:#444}
.footer .copy{position:absolute;top:325px;left:0;width:1200px;text-align:center;font-size:15px;font-weight:700}
</style>
</head>
<body>
<div class="page">

  <!-- top bar -->
  <header class="topbar">
    <div class="green"></div>
    <span class="social-dot" style="left:109px"></span>
    <span class="social-dot" style="left:156px"></span>
    <span class="social-dot" style="left:204px"></span>
    <div class="contact" style="left:715px">
      <svg width="20" height="20" viewBox="0 0 24 24"><path fill="#fff" d="M6.6 10.8a15 15 0 0 0 6.6 6.6l2.2-2.2c.3-.3.7-.4 1-.2 1.1.4 2.3.6 3.6.6.6 0 1 .4 1 1V20c0 .6-.4 1-1 1A17 17 0 0 1 3 4c0-.6.4-1 1-1h3.5c.6 0 1 .4 1 1 0 1.3.2 2.5.6 3.6.1.3 0 .7-.2 1z"/></svg>
      <span>555-014-2290</span>
    </div>
    <div class="contact" style="left:899px">
      <svg width="20" height="16" viewBox="0 0 24 18"><rect x="1" y="1" width="22" height="16" rx="2" fill="#fff"/><path d="M2 2l10 8 10-8" fill="none" stroke="#000" stroke-width="2"/></svg>
      <span style="font-weight:700">info@timberridge482.example</span>
    </div>
  </header>

  <!-- navigation -->
  <nav class="nav">
    <a class="active" style="left:109px">Home</a>
    <a style="left:187px">About Us</a>
    <a style="left:285px">Our Facility</a>
    <div class="brand"><span class="mark"></span><span class="name">TIMBER RIDGE</span></div>
    <a style="left:792px">Lessons</a>
    <a style="left:878px">Team Rental Pricing</a>
    <a style="left:1052px">More</a>
  </nav>

  <!-- hero -->
  <section class="hero" role="img" aria-label="Batter swinging in a dust cloud on a dark stage">
    <h1 class="display">WELCOME TO<br>TIMBER RIDGE</h1>
    <div class="rule-title abs" style="left:109px;top:245px;font-size:20px">BASEBALL AND SOFTBALL</div>
    <div class="btn" style="left:109px;top:285px;width:196px;height:50px">Book Appointment</div>
    <div class="dots" style="top:242px"><span class="on"></span><span></span><span></span><span></span><span></span></div>
    <svg class="abs" style="left:575px;top:552px" width="50" height="28" viewBox="0 0 50 28"><path d="M3 3l22 20L47 3" fill="none" stroke="#fff" stroke-width="4"/></svg>
  </section>

  <!-- about -->
  <section class="about">
    <div class="badge"><div class="inner" role="img" aria-label="Batter emblem on a green textured ball"></div></div>
    <h2 class="display">ABOUT US</h2>
    <div class="kicker">Who Are we?</div>
    <p>Timber Ridge is an elite baseball and softball training facility in Pine Falls. We are committed to the development of these young athletes physically, mentally and emotionally on and off the field. We are here to train, guide and mentor the youth to become the best versions of themselves. Whether their sport takes them to the next level, Timber Ridge wants to see them thrive as human beings first above all else. " Don't be afraid to be great".</p>
    <div class="sign">- <em>Timber Ridge</em> Staff</div>
    <div class="btn" style="left:624px;top:468px;width:153px;height:52px">Contact Me</div>
    <div class="dots" style="top:458px"><span></span><span class="on"></span><span></span><span></span><span></span></div>
    <div class="photo-frame" style="left:109px;top:593px;width:979px;height:324px;background:linear-gradient(180deg,#3a3d42 0%,#5a5e63 45%,#3c6b32 100%)" role="img" aria-label="Pitcher in pinstripes winding up in a stadium"></div>
  </section>

  <!-- lessons -->
  <section class="lessons">
    <h2 class="sec-title display" style="top:52px">LESSONS</h2>
    <div class="sec-sub" style="top:120px">Baseball &amp; Softball lesson pricing</div>
    <div class="dots" style="top:282px"><span></span><span></span><span class="on"></span><span></span><span></span></div>
    <div class="lesson-card" style="left:109px">
      <div class="edge"></div>
      <div class="shot" role="img" aria-label="Bat and ball resting on infield grass" style="background:linear-gradient(160deg,#6f8f5a 0%,#3f6d2a 50%,#2d5a1e 100%)"></div>
      <div class="caption">Baseball/Softball Hitting<br>Lessons : $55/30 mins</div>
    </div>
    <div class="lesson-card" style="left:633px">
      <div class="edge"></div>
      <div class="shot" role="img" aria-label="Runner sliding into base on the dirt" style="background:linear-gradient(170deg,#8c8276 0%,#a88a6c 45%,#b6957a 100%)"></div>
      <div class="caption">Baseball/ Softball Fielding/<br>Throwing Lessons: $55/30 mins</div>
    </div>
  </section>

  <!-- facility -->
  <section class="facility">
    <h2 class="sec-title display" style="top:62px">OUR FACILITY</h2>
    <div class="sec-sub" style="top:128px">You must login or create and account to be able to book a service</div>
    <div class="dots" style="top:325px"><span></span><span></span><span></span><span class="on"></span><span></span></div>
    <div class="photo-frame" style="left:109px;top:177px;width:979px;height:438px;background:radial-gradient(ellipse at 50% 45%,#6fb3e0 0%,#1f5f93 45%,#0b2a4a 85%)" role="img" aria-label="Batter swinging under stadium lights"></div>
    <div class="btn" style="left:512px;top:652px;width:241px;height:52px">Online Facility Schedule</div>
  </section>

  <!-- contact -->
  <section class="contact-sec">
    <h2 class="sec-title display" style="top:44px">CONTACT US</h2>
    <div class="sec-sub" style="top:105px">If you do not have an account please create one in order to book lessons.</div>
    <div class="dots" style="top:349px"><span></span><span></span><span></span><span></span><span class="on"></span></div>
    <div class="field" style="left:141px;top:171px;width:430px">Enter Name</div>
    <div class="field" style="left:621px;top:171px;width:430px">Enter Email</div>
    <div class="field" style="left:141px;top:274px;width:430px">Enter Phone</div>
    <div class="field" style="left:621px;top:274px;width:430px">Enter Address</div>
    <div class="field message" style="left:141px;top:373px;width:917px">Enter Message</div>
    <div class="submit">Submit</div>
  </section>

  <!-- footer -->
  <footer class="footer">
    <div class="brand-small"><span class="mark"></span><span class="name">TIMBER RIDGE</span></div>
    <div class="vline" style="left:318px"></div>
    <div class="fcol" style="left:359px">
      <h4>December Hours:</h4>
      <div class="row">
        <svg width="18" height="18" viewBox="0 0 20 20"><circle cx="10" cy="10" r="8.5" fill="none" stroke="#fff" stroke-width="1.6"/><path d="M10 5v5l3 2" fill="none" stroke="#fff" stroke-width="1.6"/></svg>
        <span style="font-size:15px;line-height:25px">Monday-Thursday&nbsp; 3:00-9:00:pm<br>Friday 4:00pm-7:00pm<br>Saturday Closed Sunday Closed</span>
      </div>
    </div>
    <div class="vline" style="left:644px"></div>
    <div class="fcol" style="left:688px">
      <h4>Contact Us</h4>
      <div class="row"><svg width="14" height="18" viewBox="0 0 14 20"><path d="M7 0a7 7 0 0 1 7 7c0 5-7 13-7 13S0 12 0 7a7 7 0 0 1 7-7z" fill="#fff"/><circle cx="7" cy="7" r="2.6" fill="#000"/></svg><span>2280 Cedar Hollow Rd Suite #100<br>PINE FALLS, CA 95000</span></div>
      <div class="row"><svg width="16" height="16" viewBox="0 0 24 24"><path fill="#fff" d="M6.6 10.8a15 15 0 0 0 6.6 6.6l2.2-2.2c.3-.3.7-.4 1-.2 1.1.4 2.3.6 3.6.6.6 0 1 .4 1 1V20c0 .6-.4 1-1 1A17 17 0 0 1 3 4c0-.6.4-1 1-1h3.5c.6 0 1 .4 1 1 0 1.3.2 2.5.6 3.6.1.3 0 .7-.2 1z"/></svg><span>555-014-2290</span></div>
      <div class="row"><svg width="16" height="13" viewBox="0 0 24 18"><rect x="1" y="1" width="22" height="16" rx="2" fill="#fff"/><path d="M2 2l10 8 10-8" fill="none" stroke="#000" stroke-width="2"/></svg><span>info@timberridge482.example</span></div>
    </div>
    <div class="vline" style="left:968px"></div>
    <div class="fcol" style="left:1016px">
      <h4>Follow Us</h4>
      <div class="row"><svg width="12" height="12" viewBox="0 0 12 12"><circle cx="6" cy="6" r="5" fill="#fff"/></svg><span>Friendbook</span></div>
      <div class="row"><svg width="12" height="12" viewBox="0 0 12 12"><circle cx="6" cy="6" r="5" fill="#fff"/></svg><span>Snapgram</span></div>
      <div class="row"><svg width="12" height="12" viewBox="0 0 12 12"><circle cx="6" cy="6" r="5" fill="#fff"/></svg><span>Chirper</span></div>
    </div>
    <div class="divider"></div>
    <div class="copy">Copyrights@2022.Timber Ridge.All Rights Reserved</div>
  </footer>

</div>
</body>
</html>
```